Awsome new website

We are a Fencing Contracting company in Melbourne Australia. We supply and install Timer and Steel boundary fences as well as Pool fencing (e.g. glass, tubular steel). We also manufacture and install swing and sliding gates.

We want a new website that is a modern business website.
We are targeting domestic and business clients.
The design should compliment our logo and company name.
The website needs to be easy to update.

Some specifics we want.
Menu - Main menu at top of page and smaller footer menu (to add different menu items)
Slider - Main page to have a slider on it that's easy for us to add and remove slides.
Call to action - all pages to have a "call to action" logo or icon that attracts attention (see file "call_to_action.pdf)
Instant quote - we have a online quote page we need a distinctive logo or icon to redirect to this page.
Main page to have a product /Service guide (see file "website_idea.jpg")
Main page to have widgets or quick link to
o why choose us
o Brochures
o Gallery

Have a Gallery page formatted with different category galleries. e.g. Timber, Glass, Feature
Maintain the current link to our staff page with password, (link in footer menu)

Hopefully that covers everything.
Our current website is www.tallgumfencing.com.au to have a look at the current site.
regards Doug

• Turn off blogging as we don’t want 100’s of comments from spammers to delete

We would like to implement the Portalio plugin (see "http://portalio-plug.net/" ), but this can be done after the new Theme has been implemented.

```html
<!DOCTYPE html>
<html lang="en">
<head>
<meta charset="utf-8">
<title>Tall Gum Fencing</title>
<link href="https://fonts.googleapis.com/css2?family=PT+Sans:wght@400;700&display=swap" rel="stylesheet">
<style>
:root{
  --red:#b3171b;
  --red-dark:#8e1114;
  --red-text:#9b1c1c;
  --gold:#ffc23a;
  --maroon:#2a0405;
  --grey-text:#6f6f6f;
  --light:#f4f4f4;
  --strip:#efefef;
  --footer:#2b2b2b;
  --white:#fff;
}
*{box-sizing:border-box;margin:0;padding:0}
html,body{width:979px;height:1200px;overflow:hidden;background:var(--white)}
body{position:relative;font-family:"PT Sans",sans-serif;color:var(--grey-text)}
.abs{position:absolute}

/* header */
.brand{left:83px;top:22px;width:175px;height:55px;display:flex;align-items:center;gap:8px;white-space:nowrap}
.brand-mark{width:14px;height:14px;background:var(--red);flex:none}
.brand-name{font-weight:700;font-size:20px;color:var(--red)}
.call-badge{left:762px;top:36px;width:139px;height:64px}
.call-badge span{position:absolute;left:42px;top:12px;font-weight:700;font-size:21px;color:var(--gold)}

/* navigation */
.nav{left:0;top:99px;width:979px;height:37px;background:linear-gradient(#c21d20,#a3141a);border-bottom:4px solid #1a0203}
.nav ul{list-style:none;position:absolute;left:83px;top:0;display:flex;height:37px}
.nav li{height:37px;line-height:40px;font-size:12.5px;color:var(--white);text-align:center;border-right:1px solid #7d0f12;border-left:1px solid #cf3235;white-space:nowrap}
.nav li.active{background:#8a0f13;position:relative}
.nav li.active::after{content:"";position:absolute;left:50%;bottom:0;margin-left:-5px;border:5px solid transparent;border-bottom-color:#1a0203}
.nav-phone{left:766px;top:99px;width:132px;height:37px;line-height:40px;text-align:right;font-size:19px;font-weight:700;color:var(--gold)}

/* hero */
.hero{left:0;top:140px;width:979px;height:411px;background:linear-gradient(#4a0709,var(--maroon) 60%,#180203)}
.hero-slide{left:81px;top:151px;width:817px;height:307px;border-radius:4px;background:linear-gradient(#7c8a4a 0%,#8e9a52 40%,#9a9488 70%,#6e7a3a 100%)}
.hero-caption{left:0;top:476px;width:979px;text-align:center;font-size:20px;color:var(--white)}
.hero-dots{left:457px;top:521px;display:flex;gap:8px}
.hero-dots i{width:10px;height:10px;border-radius:50%;background:#9a9a9a;border:1px solid #555}
.hero-dots i:first-child{background:#4a4a4a}

/* main */
h1,h2,h3{font-weight:400;color:var(--red-text)}
.welcome-title{left:83px;top:575px;font-size:22px;font-weight:700}
.welcome-text{left:83px;top:616px;width:548px;font-size:12px;line-height:20.5px;text-align:justify}
.gallery-row{left:84px;top:709px;display:flex;gap:8px}
.gallery-row div{width:177px;height:97px}
.divider{left:86px;top:822px;width:545px;height:1px;background:#ddd}
.services-title{left:83px;top:835px;font-size:18px}
.services-text{left:84px;top:869px;width:546px;font-size:10.5px;line-height:20.5px}
.service-list{list-style:none;font-size:10.8px}
.service-list li{position:absolute;padding-left:17px;white-space:nowrap}
.service-list li::before{content:"";position:absolute;left:0;top:3px;width:9px;height:9px;border-radius:50%;background:#8a8a8a}

/* sidebar */
.cta{left:660px;width:238px;height:59px;border-radius:3px;display:flex;align-items:center}
.cta-quote{top:581px;background:linear-gradient(#d02b2e,#a3141a)}
.cta-brochure{top:645px;background:linear-gradient(#5a5a5a,#2f2f2f)}
.cta .icon{width:30px;height:34px;margin:0 16px 0 26px;background:#f1f1f1;border-radius:2px}
.cta span{font-size:21px;font-weight:700;color:var(--gold);white-space:nowrap}
.why-title{left:663px;top:722px;font-size:19px}
.why-box{left:660px;top:756px;width:238px;height:252px;background:var(--light);border-top:1px solid #e2e2e2;border-bottom:1px solid #e2e2e2;padding:12px 10px 0 11px;font-size:11.5px;line-height:18.7px;text-align:justify}
.why-box p+p{margin-top:7px}
.why-box a{color:#c4181c;text-decoration:none}
.guarantee-seal{left:673px;top:915px;width:76px;height:76px;border-radius:50%;background:radial-gradient(#f8c63a 55%,#d89a12 70%,#f5c54a 100%)}
.guarantee-text{left:762px;top:933px;font-size:16px;line-height:22px;color:#444}

/* contact strip */
.contact-strip{left:0;top:1038px;width:979px;height:79px;background:var(--strip);font-size:11.5px;line-height:18.5px}
.contact-item{position:absolute;display:flex;align-items:center;gap:12px;top:20px}

/* footer */
.footer{left:0;top:1117px;width:979px;height:83px;background:var(--footer);color:#c9c9c9;font-size:11px}
.footer-menu{position:absolute;left:83px;top:18px;list-style:none;display:flex}
.footer-menu li+li::before{content:"|";margin:0 9px;color:#c9c9c9}
.copyright{position:absolute;left:83px;top:49px}
.social{position:absolute;left:792px;top:30px;display:flex;gap:8px}
.social i{width:20px;height:20px;border-radius:50%;background:#555}
</style>
</head>
<body>

<header>
  <div class="abs brand"><i class="brand-mark"></i><span class="brand-name">Tall Gum Fencing</span></div>
  <div class="abs call-badge">
    <svg width="139" height="64" viewBox="0 0 139 64">
      <path d="M4 6 L134 0 L137 44 L72 48 L64 62 L58 49 L8 50 Z" fill="#b3171b" stroke="#8e1114" stroke-width="2"/>
      <path d="M22 16 q-4 8 3 18 q8 8 14 4 l-4 -6 q-3 2 -6 -2 q-3 -4 0 -7 z" fill="#ffc23a"/>
    </svg>
    <span>CALL US</span>
  </div>
</header>

<nav class="abs nav">
  <ul>
    <li class="active" style="width:76px">HOME</li>
    <li style="width:111px">PANELSTEEL</li>
    <li style="width:129px">INSTANT QUOTE</li>
    <li style="width:89px">GALLERY</li>
    <li style="width:165px">PRODUCTS &amp; SERVICES</li>
    <li style="width:113px">CONTACT US</li>
  </ul>
</nav>
<div class="abs nav-phone">03 9044 2718</div>

<section class="abs hero"></section>
<div class="abs hero-slide" role="img" aria-label="Rural paddock with cattle grazing behind a weathered steel farm gate"></div>
<div class="abs hero-caption">PHASELLUS ERAT FELIS, SCELERISQUE A RUTRUM VITAE, MALESUADA ID ERAT</div>
<div class="abs hero-dots"><i></i><i></i><i></i><i></i></div>

<main>
  <h1 class="abs welcome-title">Welcome to Tall Gum Fencing</h1>
  <p class="abs welcome-text">Donec tincidunt gravida mauris at mollis. Nulla consectetur magna et purus porttitor, nec sollicitudin felis bibendum. Pellentesque quis malesuada risus. Vivamus vehicula feugiat porttitor. Sed pellentesque ullamcorper volutpat. Praesent volutpat augue ac sapien egestas, feugiat feugiat augue convallis. Aenean neque sapien, mollis eget auctor at, lacinia nec nulla.</p>
  <div class="abs gallery-row">
    <div role="img" aria-label="White picket garden fence on a green lawn" style="background:linear-gradient(#7a6a4e,#5e8a3a 60%,#e8ece4)"></div>
    <div role="img" aria-label="Black tubular steel fence and gate by a lake" style="background:linear-gradient(#a8b8b0,#3e5a2e 55%,#5f9a3a)"></div>
    <div role="img" aria-label="Mesh pool safety fence beside a swimming pool" style="background:linear-gradient(#4e6a3e,#7aa07a 45%,#4aa3c8)"></div>
  </div>
  <div class="abs divider"></div>
  <h2 class="abs services-title">Tall Gum Fencing Services</h2>
  <p class="abs services-text">We offer a 12 month workmanshhttp://tallgumfencing.com.au/images/site/about.jpgip warranty on our fences and wll clean the site for free of any debris from the fence construction upon completion of the job. We can offer this workmanship warranty because of our work practices, these include</p>
  <ul class="service-list">
    <li style="left:87px;top:943px">Bathroom Remodeling</li>
    <li style="left:263px;top:943px">Tile &amp; Flooring</li>
    <li style="left:390px;top:943px">Genral Home Maintenance</li>
    <li style="left:87px;top:968px">Attic &amp; Garage Finishing</li>
    <li style="left:263px;top:968px">Decks</li>
    <li style="left:390px;top:968px">Painting &amp; Wall Treatments</li>
    <li style="left:87px;top:994px">Carpentry</li>
    <li style="left:263px;top:994px">Fences</li>
    <li style="left:390px;top:994px">Drywall Install</li>
  </ul>
</main>

<aside>
  <div class="abs cta cta-quote"><i class="icon"></i><span>Get QuickQuote</span></div>
  <div class="abs cta cta-brochure"><i class="icon"></i><span>Get Our Broucher</span></div>
  <h3 class="abs why-title">Why Choose us?</h3>
  <div class="abs why-box">
    <p>Nunc bibendum nunc eget nisl molestie, eu dictum dui imperdiet. Nam a augue ac ligula pulvinar rhoncus.</p>
    <p>Nunc vitae congue lorem. Nunc ut diam sed velit sollicitudin ullamcorper in a libero. Duis iaculis vulputate nisl, vel tristique sapien scelerisque eget. <a href="#">More</a></p>
  </div>
  <div class="abs guarantee-seal"></div>
  <div class="abs guarantee-text">100% Satisfaction<br>Guarantee</div>
</aside>

<section class="abs contact-strip">
  <div class="contact-item" style="left:124px">
    <svg width="20" height="24" viewBox="0 0 20 24"><rect x="1" y="1" width="18" height="22" fill="none" stroke="#999" stroke-width="2"/><rect x="6" y="5" width="8" height="14" fill="#999"/></svg>
    <div>55, Building name, Street name<br>City - Zipcode</div>
  </div>
  <div class="contact-item" style="left:389px">
    <svg width="24" height="26" viewBox="0 0 24 26"><path d="M3 2 q-4 10 6 18 q8 6 13 3 l-2 -5 q-4 2 -8 -2 q-5 -5 -3 -9 z" fill="#999"/></svg>
    <div>Phone&nbsp;&nbsp;&nbsp;: 503.410.2286<br>Toll Free: 888.615.3042</div>
  </div>
  <div class="contact-item" style="left:642px;top:28px">
    <svg width="22" height="16" viewBox="0 0 22 16"><rect width="22" height="16" fill="#999"/><path d="M0 0 L11 9 L22 0" fill="none" stroke="#efefef" stroke-width="1.5"/></svg>
    <div>E-mail : info@tallgumfencing.com.au</div>
  </div>
</section>

<footer class="abs footer">
  <ul class="footer-menu">
    <li>Home</li><li>Panelsteel</li><li>Instant Quote</li><li>Gallery</li><li>Products &amp; Services</li><li>Contact us</li>
  </ul>
  <div class="copyright">Copyright &copy; 2013&nbsp;&nbsp; Tall Gum Fencing.&nbsp;&nbsp; All rights reserved.</div>
  <div class="social"><i></i><i></i><i></i><i></i></div>
</footer>

</body>
</html>
```